RWT Fittings Ltd Business Cards

We need a business card with our business logo. We provide window and door installations on high-rises in west coast British Colombia, Canada.

I would like my business information and details on one side of the card, and the other side the company name with logo

Target Market(s)

General Contractors

Industry/Entity Type

Construction

Contact Information for Business Card

one side i want my company name and logo in the dark theme logo that i provided

Requirements
Must have
• Marco Peltieri, 16045518293, RWTFittings@mailbox-demo.com, 1407-5194 Linden Row Burnaby BC, V5H 2K9, Owner & Manager

```html
<!DOCTYPE html>
<html lang="en">
<head>
<meta charset="utf-8">
<title>RWT Fittings Ltd – Business Card</title>
<link href="https://fonts.googleapis.com/css2?family=Open+Sans:wght@400;600;700&display=swap" rel="stylesheet">
<style>
  :root {
    --page: #d9d9db;
    --card: #1c1c1e;
    --card-deep: #141415;
    --accent: #29a8e0;
    --text: #dedede;
    --muted: #9a9a9c;
    --decor-a: #2a2a2c;
    --decor-b: #1e1e20;
  }
  * { box-sizing: border-box; margin: 0; padding: 0; }
  html, body {
    width: 1200px; height: 780px; overflow: hidden;
    background: var(--page);
    font-family: "Open Sans", Arial, sans-serif;
  }
  .sheet {
    width: 1200px; height: 780px;
    display: flex; align-items: center; justify-content: center; gap: 40px;
  }
  .card {
    position: relative;
    width: 535px; height: 306px;
    background: var(--card);
    border-radius: 22px;
    overflow: hidden;
  }
  /* front */
  .card-front .brand {
    position: absolute; left: 150px; top: 34px; z-index: 1;
    display: flex; align-items: center; gap: 10px;
  }
  .brand-square {
    width: 22px; height: 22px; background: var(--accent);
  }
  .brand-name {
    font-weight: 700; font-size: 25px; color: var(--accent); letter-spacing: 0.5px;
    white-space: nowrap;
  }
  .person {
    position: absolute; left: 30px; top: 100px; z-index: 1;
  }
  .person-name {
    position: relative;
    padding-left: 24px;
    font-weight: 600; font-size: 21px; line-height: 26px;
    color: var(--accent); text-transform: uppercase; white-space: nowrap;
  }
  .person-name::before {
    content: ""; position: absolute; left: 0; top: 0;
    width: 10px; height: 46px; background: var(--accent);
  }
  .person-role {
    padding-left: 24px;
    font-size: 14px; line-height: 20px; color: var(--text);
  }
  .address {
    margin-top: 14px; padding-left: 24px;
    font-size: 14px; line-height: 20px; color: var(--text);
  }
  .contacts {
    list-style: none; margin-top: 12px; padding-left: 4px;
  }
  .contacts li {
    display: flex; align-items: center; gap: 7px;
    font-size: 14px; line-height: 21px; color: var(--text); white-space: nowrap;
  }
  .contacts svg { width: 12px; height: 12px; flex: none; }
  .front-decor {
    position: absolute; right: 0; bottom: 0; z-index: 0;
    width: 225px; height: 180px;
    background: linear-gradient(135deg, var(--decor-b) 0%, var(--decor-a) 55%, var(--decor-b) 100%);
    border-top-left-radius: 110px;
  }
  /* back */
  .card-back .back-decor {
    position: absolute; inset: 0;
    background: linear-gradient(135deg, var(--decor-a) 0%, var(--card-deep) 60%, var(--card) 100%);
  }
  .card-back .brand {
    position: absolute; inset: 0;
    display: flex; align-items: center; justify-content: center; gap: 10px;
  }
</style>
</head>
<body>
<main class="sheet">

  <section class="card card-front" aria-label="Business card front">
    <div class="front-decor" role="img" aria-label="Large faint company mark decoration"></div>

    <div class="brand">
      <span class="brand-square"></span>
      <span class="brand-name">RWT Fittings Ltd</span>
    </div>

    <div class="person">
      <h1 class="person-name">Marco Peltieri</h1>
      <p class="person-role">Owner &amp; Manager</p>
      <p class="address">1407-5194 Linden Row<br>Burnaby BC, V5H 2K9</p>
      <ul class="contacts">
        <li>
          <svg viewBox="0 0 12 12" aria-hidden="true"><path fill="var(--accent)" d="M2.5 1h2l1 2.6-1.3 1a6.5 6.5 0 0 0 3.2 3.2l1-1.3L11 7.5v2A1.5 1.5 0 0 1 9.5 11 8.5 8.5 0 0 1 1 2.5 1.5 1.5 0 0 1 2.5 1z"/></svg>
          16045518293
        </li>
        <li>
          <svg viewBox="0 0 12 12" aria-hidden="true"><rect x="0.5" y="2" width="11" height="8" fill="var(--accent)"/><path d="M0.5 2.5 6 6.5l5.5-4" stroke="var(--card)" stroke-width="1" fill="none"/></svg>
          RWTFittings@mailbox-demo.com
        </li>
        <li>
          <svg viewBox="0 0 12 12" aria-hidden="true"><circle cx="6" cy="6" r="5.5" fill="var(--accent)"/><path d="M0.5 6h11M6 0.5c-2.6 2.8-2.6 8.2 0 11M6 0.5c2.6 2.8 2.6 8.2 0 11" stroke="var(--card)" stroke-width="0.8" fill="none"/></svg>
          www.rwtfittings-demo.com
        </li>
      </ul>
    </div>
  </section>

  <section class="card card-back" aria-label="Business card back">
    <div class="back-decor" role="img" aria-label="Repeating tonal pattern of the company mark"></div>
    <div class="brand">
      <span class="brand-square"></span>
      <span class="brand-name">RWT Fittings Ltd</span>
    </div>
  </section>

</main>
</body>
</html>
```